Improve Wine Bottle Label, Glass Printed Naked Lady, Elegant, Classy, Professional

We are transitioning our labelling method over to glass screen-printing.We have an existing label (attached image1 -ai also attached) that we think is cool, but moving forward we would like a more professional looking design that is classy, artsy, but still high impact (one very rough idea is attached). The bottle is remaining the same size. The cap is the same pink colour. Title of wine is Saffron Kestrel' Front Text needs to include:2018 MontepulcianoEden Valley - Barossa The graphic must contain a tasteful (arty) and attractive naked woman. Design colours that are preferred are:Hot Pink - as seen in imageDark Blue - as seen in imageMatte White** Note that colours are single, shading etc is not easily possible due to the screen printing method. - view process on our instagram page. https://www.pictura.example/dalrowvino/- please also look at this page to see our other recent labels, so ascertain our style/audience.You do not need to have all the colours, if your submission looks great with 1 or 2. feel free to keep it this way. Dimensions.The glass printer can print within 10mm of the base of the bottle, and 10mm of the shoulder of the bottle. Height 150mmIt can print the full circumference of the bottle up to approx 30mm gap. (Max 208mm) - see our gold label on the instagram page. - however, imagine this bottle in a store - we need customers to be able to see the image and title on one side. So if you decide to wrap around the bottle, it needs to achieve the requirements whilst only seeing the Title side of the bottle. We have found this to be about 90mm wide maximum.

Target Market(s)

Wine Consumers

Industry/Entity Type

Winery

Font styles to use
Serif
Sans Serif

Colors
e34297
3176b5
ffffff

Requirements
Must have
• Colours, Title, Text - as stated
• Naked arty woman
• Single colours - NO SHADING
Nice to have
• Our Logo integrated smoothly - only do this if you can do it well.

```html
<!DOCTYPE html>
<html lang="en">
<head>
<meta charset="utf-8">
<title>Saffron Kestrel – 2018 Montepulciano bottle design</title>
<link rel="stylesheet" href="https://fonts.googleapis.com/css2?family=Marcellus&family=Tinos:wght@400;700&display=swap">
<style>
  :root {
    --paper: #ffffff;
    --frame: #8a8a8a;
    --glass: #1c0c10;
    --cap-light: #c06aae;
    --cap-dark: #c4368f;
    --band-light: #d0609f;
    --band-dark: #c4368f;
    --ink: #ffffff;
  }
  html, body {
    margin: 0;
    padding: 0;
    width: 870px;
    height: 1200px;
    overflow: hidden;
    background: var(--paper);
  }
  .sheet { display: block; width: 870px; height: 1200px; }
  .sheet-frame { fill: none; stroke: var(--frame); stroke-width: 2; }
  .bottle-glass { fill: var(--glass); }
  .bottle-sheen { fill: #ffffff; opacity: 0.06; }
  .cap-light { fill: var(--cap-light); }
  .cap-dark { fill: var(--cap-dark); }
  .band-light { fill: var(--band-light); }
  .band-dark { fill: var(--band-dark); }
  .figure-area { fill: var(--band-dark); }
  .brand-mark { fill: none; stroke: var(--ink); stroke-width: 1.5; }
  .brand-name { fill: var(--ink); font-family: "Tinos", serif; font-weight: 400; }
  .wine-title {
    fill: var(--ink);
    font-family: "Marcellus", serif;
    font-size: 33px;
    letter-spacing: 1px;
  }
  .wine-detail { fill: var(--ink); font-family: "Tinos", serif; font-size: 16px; }
  .back-line { fill: var(--ink); font-family: "Tinos", serif; font-size: 8.5px; }
  .back-strong { font-weight: 700; }
  .volume { fill: var(--ink); font-family: "Tinos", serif; font-weight: 700; font-size: 13px; }
  .drinks-icon { fill: none; stroke: var(--ink); stroke-width: 1.3; }
  .drinks-text { fill: var(--ink); font-family: "Tinos", serif; font-size: 6px; }
</style>
</head>
<body>
<svg class="sheet" viewBox="0 0 870 1200" xmlns="http://www.w3.org/2000/svg">
  <defs>
    <clipPath id="front-body">
      <path d="M232,240 L320,240 L322,290 C326,350 403,360 403,440 L403,1112 Q403,1124 391,1124 L174,1124 Q162,1124 162,1112 L162,440 C162,360 226,350 230,290 Z"/>
    </clipPath>
    <clipPath id="back-body">
      <path d="M514,240 L602,240 L604,290 C608,350 685,360 685,440 L685,1112 Q685,1124 673,1124 L456,1124 Q444,1124 444,1112 L444,440 C444,360 508,350 512,290 Z"/>
    </clipPath>
  </defs>

  <rect class="sheet-frame" x="5" y="5" width="860" height="1190"/>

  <!-- Front bottle -->
  <g class="bottle bottle-front">
    <g clip-path="url(#front-body)">
      <rect class="bottle-glass" x="150" y="230" width="270" height="910"/>
      <rect class="bottle-sheen" x="184" y="420" width="12" height="680" rx="6"/>
      <polygon class="band-light" points="150,548 230,548 230,650 150,712"/>
      <polygon class="band-dark" points="230,548 410,548 230,650"/>
    </g>
    <path class="cap-dark" d="M228,58 Q228,48 238,48 L315,48 Q325,48 325,58 L325,252 L228,252 Z"/>
    <path class="cap-light" d="M228,58 Q228,48 238,48 L266,48 L266,252 L228,252 Z"/>

    <rect class="figure-area" x="174" y="618" width="140" height="218" rx="4"
          role="img" aria-label="Single-colour pink illustration of a woman's legs in high heels stepping out from beneath the band"/>

    <g class="brand brand-front">
      <circle class="brand-mark" cx="328" cy="637" r="5"/>
      <text class="brand-name" x="337" y="642" font-size="15">Dalrow</text>
    </g>

    <text class="wine-title" x="234" y="892">SAFFRON</text>
    <text class="wine-title" x="234" y="932">KESTREL</text>
    <text class="wine-detail" x="234" y="985">2018 Montepulciano</text>
    <text class="wine-detail" x="234" y="1016">Eden Valley - Barossa</text>
  </g>

  <!-- Back bottle -->
  <g class="bottle bottle-back">
    <g clip-path="url(#back-body)">
      <rect class="bottle-glass" x="432" y="230" width="270" height="910"/>
      <rect class="bottle-sheen" x="466" y="420" width="12" height="680" rx="6"/>
      <polygon class="band-light" points="444,548 528,548 528,604"/>
      <polygon class="band-dark" points="528,548 690,548 690,711 528,604"/>
    </g>
    <path class="cap-dark" d="M510,58 Q510,48 520,48 L597,48 Q607,48 607,58 L607,252 L510,252 Z"/>
    <path class="cap-light" d="M510,58 Q510,48 520,48 L548,48 L548,252 L510,252 Z"/>

    <g class="brand brand-back">
      <circle class="brand-mark" cx="532" cy="876" r="6"/>
      <text class="brand-name" x="544" y="884" font-size="24">Dalrow</text>
    </g>

    <text class="back-line back-strong" x="568" y="919" text-anchor="middle">WINE OF AUSTRALIA</text>
    <text class="back-line" x="568" y="935" text-anchor="middle">dalrowvino.example</text>
    <rect x="515" y="944" width="8" height="8" fill="#ffffff"/>
    <text class="back-line" x="527" y="950">Find us on Pictura</text>
    <text class="back-line back-strong" x="515" y="961">Dalrow Brothers Wine Sales</text>

    <text class="back-line" x="515" y="993" font-size="7.5">15.4% ALC/VOL</text>
    <text class="volume" x="515" y="1007">750mL</text>

    <g class="standard-drinks">
      <path class="drinks-icon" d="M612,972 L628,972 L627,988 Q620,995 613,988 Z M620,993 L620,1006 M613,1007 L627,1007"/>
      <text class="drinks-text" x="620" y="984" text-anchor="middle">9.1</text>
      <text class="drinks-text" transform="translate(606,1008) rotate(-90)">Std Drinks</text>
    </g>
  </g>
</svg>
</body>
</html>
```